Quiet Hollow is a cabin in Gatlinburg, Tennessee, near the Ferncrest Ridge National Park. When our cabin was built, there was one thing more important than any other--peace. The front of our cabin is surrounded by woods. It has a huge deck with a swing, Adirondack chairs, and a love seat for relaxation. The back deck has a hot tub, a large round glass table for cocktails or dinner, and because we left no stone unturned, we have a telescope for stargazing. There are two master suites, each have a private bath with a large jetted tub, seperate shower, flat screen TV, and a door that leads to the back deck.

Industry/Entity Type

Business

Contact Information for Business Card

Quiet Hollow Vacation Rentals, LLC
871 Belford Crest Pl.
Oakland, Ky 42159
Janet M. Pruitt, Owner/Manager
(270) 614.2087

```html
<!DOCTYPE html>
<html lang="en">
<head>
<meta charset="utf-8">
<title>Quiet Hollow Vacation Rentals — Business Card</title>
<link rel="stylesheet" href="https://fonts.googleapis.com/css2?family=Lato:wght@400;700&display=swap">
<style>
  :root {
    --stage: #3a3330;
    --card: #111111;
    --card-edge: #1c1c1c;
    --orange: #f7941d;
    --green: #3fb449;
    --silver: #d4d4d4;
    --silver-dim: #9a9a9a;
    --divider: #2a2a2a;
  }
  * { margin: 0; padding: 0; box-sizing: border-box; }
  html, body { width: 1200px; height: 844px; overflow: hidden; }
  body {
    background: var(--stage);
    font-family: "Lato", sans-serif;
    position: relative;
  }
  .card {
    position: absolute;
    top: 272px;
    width: 520px;
    height: 300px;
    background: var(--card);
    border: 1px solid var(--card-edge);
    border-radius: 3px;
  }
  .card--front { left: 50px; }
  .card--back { left: 630px; }

  .brand {
    position: absolute;
    display: flex;
    flex-direction: column;
    align-items: center;
    text-align: center;
  }
  .brand__mark {
    width: 46px;
    height: 46px;
    border-radius: 50%;
    border: 3px solid #3a3a3a;
    margin-bottom: 14px;
  }
  .brand__name {
    font-weight: 700;
    font-size: 18px;
    line-height: 1.3;
    letter-spacing: 0.5px;
    text-transform: uppercase;
    color: var(--silver);
    white-space: nowrap;
  }
  .card--front .brand { left: 16px; top: 92px; width: 236px; }
  .card--back .brand { left: 120px; top: 96px; width: 280px; }
  .card--back .brand__mark { width: 52px; height: 52px; border-color: var(--silver-dim); }

  .card__divider {
    position: absolute;
    left: 262px;
    top: 20px;
    bottom: 20px;
    width: 1px;
    background: var(--divider);
  }
  .contact {
    position: absolute;
    left: 282px;
    top: 82px;
    font-size: 14px;
    line-height: 1.35;
    color: var(--orange);
  }
  .contact__name { font-size: 20px; line-height: 1.15; }
  .contact__role { color: var(--green); font-size: 13px; margin-bottom: 14px; }
  .contact__address { margin-bottom: 12px; }
  .contact__label { color: var(--green); }
</style>
</head>
<body>
  <section class="card card--front" aria-label="Card front">
    <div class="brand">
      <span class="brand__mark"></span>
      <p class="brand__name">Quiet Hollow<br>Vacation Rentals, LLC</p>
    </div>
    <div class="card__divider"></div>
    <div class="contact">
      <p class="contact__name">Janet M. Pruitt</p>
      <p class="contact__role">Owner/Manager</p>
      <p class="contact__address">871 Belford Crest Pl.<br>Oakland, Ky 42159</p>
      <p><span class="contact__label">T:</span> (270) 614.2087</p>
    </div>
  </section>

  <section class="card card--back" aria-label="Card back">
    <div class="brand">
      <span class="brand__mark"></span>
      <p class="brand__name">Quiet Hollow<br>Vacation Rentals, LLC</p>
    </div>
  </section>
</body>
</html>
```